A tri fold flyer to be sent to parents advertising Learning Center, tutoring in math or language after school and on weekendsSince 1994 the Bright Owl Study House has been helping the children on Oahu do better in school. Bright Owl has developed a successful method of teaching math, reading and writing for students in grades K-12. Affordable and effective, it's unlike any other learning system.

Target Market(s)

Parents of school age kids

Industry/Entity Type

Education

Font styles to use
Sans Serif

Requirements
Must have
• same text as in previews
Nice to have
• 3 fold
Should not have
• mistakes

```html
<!DOCTYPE html>
<html lang="en">
<head>
<meta charset="utf-8">
<title>Bright Owl Study House – Tri-fold Flyer</title>
<link rel="stylesheet" href="https://fonts.googleapis.com/css2?family=Oswald:wght@600;700&family=PT+Sans:wght@400&display=swap">
<style>
  :root {
    --royal: #1a2fd6;
    --gold: #f7c51a;
    --ink: #1f1f1f;
    --white: #ffffff;
    --band-light: #3fa6e6;
    --band-mid: #2a8fd6;
    --band-dark: #1470b8;
  }
  * { margin: 0; padding: 0; box-sizing: border-box; }
  html, body { width: 1200px; height: 934px; overflow: hidden; background: var(--white); }
  .flyer {
    position: relative; width: 1200px; height: 934px; overflow: hidden;
    background: var(--white);
    font-family: "PT Sans", Arial, sans-serif;
  }
  .photo { position: absolute; }
  .photo--tutor-boy {
    left: 0; top: 0; width: 400px; height: 560px;
    background: linear-gradient(135deg, #eef3f4 0%, #d9e4ea 40%, #b9cfe0 70%, #e8dcc8 100%);
  }
  .photo--team {
    left: 789px; top: 0; width: 411px; height: 258px;
    background: linear-gradient(160deg, #c9c2b5 0%, #2746b8 45%, #1d36a6 75%, #2a2a3a 100%);
  }
  .photo-divider {
    position: absolute; left: 789px; top: 258px; width: 411px; height: 7px; background: var(--gold);
  }
  .photo--high-five {
    left: 789px; top: 265px; width: 411px; height: 290px;
    background: linear-gradient(120deg, #b9d2c4 0%, #d8c3a8 40%, #e9e4dc 70%, #cfd8d6 100%);
  }
  .headline {
    position: absolute; left: 442px; top: 70px;
    font-family: "Oswald", "Arial Narrow", sans-serif; font-weight: 700;
    font-size: 45px; line-height: 57px; color: var(--royal);
    text-transform: uppercase; letter-spacing: 0.5px;
  }
  .headline .accent { color: var(--gold); }
  .intro {
    position: absolute; left: 449px; top: 212px; width: 292px;
    font-size: 25px; line-height: 35.5px; color: var(--ink);
    text-align: justify;
  }
  .call {
    position: absolute; left: 449px; top: 418px;
    font-family: "Oswald", "Arial Narrow", sans-serif; font-weight: 700;
    font-size: 45px; color: var(--gold); letter-spacing: 0.5px;
  }
  .wave { position: absolute; left: 0; top: 0; }
  .column {
    position: absolute; top: 622px; width: 333px;
    font-size: 15px; line-height: 22.2px; color: var(--white);
    text-align: justify;
  }
  .column p + p { margin-top: 22px; }
  .column--history { left: 36px; }
  .column--method { left: 434px; top: 618px; }
  .column--lessons { left: 829px; top: 618px; }
  .tagline {
    margin-top: 18px; font-size: 25px; line-height: 36px; color: var(--gold); text-align: left;
  }
</style>
</head>
<body>
<main class="flyer">
  <div class="photo photo--tutor-boy" role="img" aria-label="Photo of a tutor sitting beside a young boy with an open book"></div>
  <div class="photo photo--team" role="img" aria-label="Group photo of the tutoring staff in matching blue shirts"></div>
  <div class="photo-divider"></div>
  <div class="photo photo--high-five" role="img" aria-label="Photo of a smiling girl giving her tutor a high five in class"></div>

  <h1 class="headline">The Bright <span class="accent">Owl</span><br>Study House</h1>
  <p class="intro">in Pearl City has developed a successful method of teaching math, reading and writing for students in grades K-12.</p>
  <p class="call">CALL 455-0192</p>

  <svg class="wave" width="1200" height="934" viewBox="0 0 1200 934" aria-hidden="true">
    <defs>
      <linearGradient id="bandFill" x1="0" y1="0" x2="1" y2="0.3">
        <stop offset="0" stop-color="var(--band-mid)"/>
        <stop offset="0.45" stop-color="var(--band-light)"/>
        <stop offset="1" stop-color="var(--band-dark)"/>
      </linearGradient>
    </defs>
    <path d="M0 548 C140 548 300 545 404 520 C520 510 620 560 760 555 C900 548 1050 520 1200 580 L1200 934 L0 934 Z" fill="var(--white)"/>
    <path d="M0 540 C140 548 300 545 404 518 C520 508 620 556 760 551 C900 544 1050 516 1200 574 L1200 596 C1050 540 900 560 760 568 C620 574 520 530 404 532 C300 560 140 566 0 556 Z" fill="var(--gold)"/>
    <path d="M0 566 C140 576 300 570 404 542 C520 540 620 584 760 578 C900 572 1050 552 1200 604 L1200 934 L0 934 Z" fill="url(#bandFill)"/>
  </svg>

  <section class="column column--history">
    <p>Since 1994 the Bright Owl Study House has been helping the children on Oahu do better in school. Bright Owl has developed a successful method of teaching math, reading and writing for students in grades K-12. Affordable and effective, it's unlike any other learning system. Rather than simply walking students through worksheets or being a homework assistant, Bright Owl is a productive and exciting way to learn.</p>
    <p>Lessons are designed to accommodate students</p>
  </section>

  <section class="column column--method">
    <p>at any ability level. All students (remedial, average and gifted) benefit because the programs are personalized. Pre and post tests measure the student's progress.</p>
    <p>Outstanding improvement is made because every lesson is designed to challenge the student while ensuring that a specific skill is mastered. Lessons are extended hour long (70 minutes), most kids come twice a week; the charge is $35 per lesson.</p>
  </section>

  <section class="column column--lessons">
    <p>Each lesson has a variety of learning activities, which include personalized instruction, hands on manipulatives and individual computer sessions. This multisensory method of instruction provides the maximum amount of learning in the minimum amount of time.</p>
    <p class="tagline">Bright Owl students have experience of being successful, which builds their confidence.</p>
  </section>
</main>
</body>
</html>
```